Business Card Design Project

Looking to update our business cards. We have a logo with our slogan. We are an IT firm so we wouldlike a modern look.

Industry/Entity Type

Business

```html
<!DOCTYPE html>
<html lang="en">
<head>
<meta charset="utf-8">
<title>Novaloop Inc — Business Card</title>
<link rel="stylesheet" href="https://fonts.googleapis.com/css2?family=Jost:wght@400;500&family=Tinos&display=swap">
<style>
  :root {
    --page-bg: #3a2620;
    --green-light: #9bbb41;
    --green-mid: #7f9d38;
    --green-edge: #6a8533;
    --band-light: #f4f4f4;
    --band-shade: #d6d6d6;
    --brand-green: #56692a;
    --ink-dark: #1e1e1e;
    --contact-ink: #2b3614;
  }
  * { margin: 0; padding: 0; box-sizing: border-box; }
  html, body {
    width: 1200px;
    height: 771px;
    overflow: hidden;
    background: var(--page-bg);
  }
  .business-card {
    position: absolute;
    left: 50px;
    top: 70px;
    width: 1100px;
    height: 631px;
    background: radial-gradient(ellipse 60% 65% at 50% 48%, var(--green-light) 0%, var(--green-mid) 55%, var(--green-edge) 100%);
    box-shadow: 0 10px 30px rgba(0,0,0,0.45);
    overflow: hidden;
  }
  .brand-band {
    position: absolute;
    left: 0;
    top: 238px;
    width: 100%;
    height: 155px;
    background: linear-gradient(180deg, var(--band-shade) 0%, var(--band-light) 30%, var(--band-light) 65%, var(--band-shade) 100%);
    box-shadow: 0 4px 8px rgba(0,0,0,0.25), 0 -2px 4px rgba(0,0,0,0.1);
  }
  .brand-name {
    position: absolute;
    left: 0;
    top: 24px;
    width: 100%;
    text-align: center;
    font-family: "Jost", sans-serif;
    font-weight: 500;
    font-size: 62px;
    line-height: 1;
    letter-spacing: 10px;
    color: var(--brand-green);
  }
  .brand-slogan {
    position: absolute;
    left: 0;
    top: 106px;
    width: 100%;
    text-align: center;
    font-family: "Jost", sans-serif;
    font-weight: 500;
    font-size: 22px;
    letter-spacing: 5.5px;
    color: var(--ink-dark);
  }
  .contact-row {
    position: absolute;
    left: 37px;
    right: 37px;
    top: 592px;
    display: flex;
    justify-content: space-between;
    font-family: "Tinos", serif;
    font-size: 21px;
    color: var(--contact-ink);
  }
  .contact-item { display: flex; align-items: center; gap: 12px; }
  .contact-bullet {
    width: 11px;
    height: 11px;
    background: var(--contact-ink);
  }
</style>
</head>
<body>
  <main class="business-card">
    <section class="brand-band">
      <h1 class="brand-name">NOVALOOP INC</h1>
      <p class="brand-slogan">KEEPING COMPUTING SIMPLE</p>
    </section>
    <footer class="contact-row">
      <div class="contact-item"><span>Phone</span><span class="contact-bullet"></span><span>0123456789</span></div>
      <div class="contact-item"><span>Web</span><span class="contact-bullet"></span><span>www.website.com</span></div>
      <div class="contact-item"><span>Email</span><span class="contact-bullet"></span><span>name@email.com</span></div>
    </footer>
  </main>
</body>
</html>
```